Web Design Project

I need a three page website. I have designed the index.html and the specialevent.html page.

I need someone to finetune the pages for me.

Where I have difficulty is with the following:
I want to add an event table driven by php database.
The administrator of the event will login and create the wording that fits under each colmn. The administrator the submit the form to php database. The database then display in a html.

The Table contains 5 coloums and the rows can vary and can go up to as many as 100.

The table set out events on a program
In the last column of every row I need a submit button to "View and Book" I need to link those buttons with external links/pages.

I use Dreamweaver CS5 and I need to have it in this format in order for me to edit it in the future.

The Table needs to be updated once a year for this program. So ideally if someone has a password to update the certain regions this is what I have in mind.

I have also designed a mockup of the restaurant page. At the top I need.
1) 4 Colapsable panels
a) Restaurants - opening the names of the restaurants
b) Coffee shops and light lunches .... with the names
c) Family
d) Home eateries

From the colapsable panel of each of these I need a anchored link to the description/photos of each...with a BOOK now button I can submit bookings to.

I added a colapsable panel in each restaurants description to keep everything contained.

Please help

• Background must be fixed so that main.div scroll over it

The colours are chosen so please stick to it.

The green for the submit button I short is. #C8D707

I need to edit the pages in Dreamweaver CS5. /Flexilayout2pro

Please ask if you need to know anything. I exactly know what I want.

Kind regards
Pieter Vansloten

The colours are fine.

The wording " karoovistadirect BOOKING agent" should appear right at the top in the white horizon part of the background image.

The specialevent page I described already. I am interested in the editable solution. for this.

I will make up a mockup of the third page and send it later.

Regards

```html
<!DOCTYPE html>
<html lang="en">
<head>
<meta charset="utf-8">
<title>Karoovistadirect – Your booking agent</title>
<link rel="stylesheet" href="https://fonts.googleapis.com/css2?family=Oswald:wght@300;400;500&family=PT+Sans:ital,wght@0,400;0,700;1,400&display=swap">
<style>
  :root{
    --lime:#c8d707;
    --lime-dark:#a3b400;
    --olive:#7b8b0f;
    --olive-text:#93a800;
    --orange:#ff6a1f;
    --orange-deep:#f2501e;
    --blue:#1a9ad6;
    --blue-deep:#1277bf;
    --panel:#2f2f2f;
    --ink:#1a1a1a;
    --night:#141414;
    --text:#555;
    --muted:#a9a9a9;
    --white:#fff;
  }
  *{box-sizing:border-box;margin:0;padding:0}
  html,body{width:1200px;height:1100px;overflow:hidden}
  body{position:relative;background:var(--night);font-family:"PT Sans",Arial,sans-serif;color:var(--text)}
  .heading{font-family:"Oswald",Arial Narrow,sans-serif;font-weight:400;text-transform:uppercase}
  .landscape{position:absolute;inset:0 0 auto 0;height:760px;
    background:linear-gradient(180deg,#fff 0,#f5f5f5 60px,#bdbdbd 110px,#8d8d8d 200px,#7a7a7a 380px,#9a9a9a 470px,#6e6e6e 580px,#3a3a3a 690px,var(--night) 760px)}
  .brand{position:absolute;left:128px;top:16px;font-family:"Oswald",sans-serif;font-weight:400;font-size:34px;letter-spacing:-.5px;color:var(--lime)}
  .mainnav{position:absolute;left:120px;top:83px;width:960px;height:40px;border-radius:20px;
    background:linear-gradient(180deg,#d6e41d,#b2c300);border:2px solid #9fb000;box-shadow:0 2px 3px rgba(0,0,0,.35)}
  .mainnav a{position:absolute;top:0;height:36px;line-height:36px;color:var(--white);text-decoration:none;font-family:"Oswald",sans-serif;font-size:14px;text-transform:uppercase}
  .mainnav .current{left:0;width:72px;text-align:center;background:#2a2a2a;border-radius:18px 0 0 18px}
  .search{position:absolute;right:4px;top:3px;width:210px;height:30px;border-radius:15px;background:var(--white);border:2px solid #e4ec9a;box-shadow:inset 0 2px 3px rgba(0,0,0,.25)}
  .search svg{position:absolute;right:14px;top:8px}
  .booking{position:absolute;left:120px;top:132px;width:960px;height:340px;background:var(--panel);border-radius:6px}
  .booking h2{position:absolute;left:9px;top:14px;font-family:"Oswald",sans-serif;font-weight:400;font-style:italic;font-size:19px;color:var(--lime)}
  .card{position:absolute;top:57px;width:300px;height:271px;background:var(--white);border-radius:6px}
  .card .tile{position:absolute;left:8px;top:10px;width:280px;height:130px;border-radius:6px;display:flex;align-items:center;justify-content:center;
    font-family:"Oswald",sans-serif;font-size:40px;color:var(--white);box-shadow:0 2px 3px rgba(0,0,0,.3)}
  .tile .light{font-weight:300}
  .tile .bold{font-weight:500}
  .stay{background:linear-gradient(180deg,#ff8437,var(--orange-deep))}
  .play{background:linear-gradient(180deg,var(--lime),var(--lime-dark))}
  .eat{background:linear-gradient(180deg,#22aadf,var(--blue-deep))}
  .card p{position:absolute;left:10px;right:10px;top:160px;text-align:center;font-size:17px;line-height:24px;color:#666}
  .events{position:absolute;left:120px;top:492px;width:960px;height:262px;background:var(--white);border-radius:6px}
  .events h2{position:absolute;left:10px;top:12px;font-size:19px;color:var(--orange-deep)}
  .rule{position:absolute;left:10px;width:940px;height:1px;background:#e2e2e2}
  .event{position:absolute;left:10px;width:940px;height:62px}
  .date{position:absolute;left:0;top:0;width:70px;height:60px;border-radius:6px;background:linear-gradient(180deg,#3b3b3b,#1d1d1d);
    text-align:center;font-family:"Oswald",sans-serif;font-weight:300;color:var(--white);box-shadow:0 2px 3px rgba(0,0,0,.3)}
  .date .day{display:block;font-size:17px;line-height:20px;margin-top:8px;color:var(--lime)}
  .date .month{display:block;font-size:15px;line-height:20px}
  .event h3{position:absolute;left:81px;top:0;font-weight:400;font-size:16px;color:var(--olive-text)}
  .event p{position:absolute;left:80px;top:26px;width:862px;font-size:11.6px;line-height:18px;color:#333}
  .contact{position:absolute;left:120px;top:768px}
  .footer-title{font-size:21px;color:var(--lime)}
  .contact-line{position:absolute;font-family:"Oswald",sans-serif;font-weight:300;font-size:13.5px;line-height:17px;color:var(--muted);text-transform:uppercase;white-space:nowrap}
  .follow{position:absolute;left:935px;top:768px}
  .social{position:absolute;top:38px;width:30px;height:30px}
  .siteinfo{position:absolute;left:120px;top:879px;width:960px;height:199px;border-radius:6px;overflow:hidden;
    background:linear-gradient(180deg,var(--lime),#aebe00);border:1px solid #9aab00}
  .legal{height:41px;line-height:40px;padding-left:10px;background:var(--olive);color:var(--white);font-size:14px}
  .services{position:absolute;left:10px;top:56px;width:381px}
  .services h4,.newsletter h4{font-family:"Oswald",sans-serif;font-weight:400;font-size:15px;color:var(--ink);text-transform:uppercase}
  .services ul{list-style:none;margin-top:11px}
  .services li{border-top:1px solid #7f8c00;height:35px;line-height:35px;font-size:13px;color:var(--ink)}
  .newsletter{position:absolute;left:628px;top:56px}
  .newsletter .field{position:absolute;left:0;top:35px;width:304px;height:36px;border-radius:18px;background:var(--white);border:2px solid #e9f09e;box-shadow:inset 0 2px 3px rgba(0,0,0,.25)}
  .newsletter .signup{position:absolute;left:209px;top:86px;width:95px;height:36px;border-radius:18px;background:var(--ink);color:var(--lime);
    font-family:"Oswald",sans-serif;font-size:16px;text-align:center;line-height:34px;border:1px solid #000}
</style>
</head>
<body>
  <div class="landscape" role="img" aria-label="Black and white photograph of a Karoo valley landscape with hills, a winding road and the village below"></div>

  <header>
    <div class="brand">KAROOVISTADIRECT</div>
    <nav class="mainnav">
      <a class="current" href="#">Home</a>
      <a href="#" style="left:92px">Accommodation</a>
      <a href="#" style="left:223px">Play</a>
      <a href="#" style="left:288px">Contact</a>
      <div class="search">
        <svg width="11" height="11" viewBox="0 0 11 11"><circle cx="7" cy="4" r="3" fill="none" stroke="#777" stroke-width="1.5"/><line x1="5" y1="6" x2="1" y2="10" stroke="#777" stroke-width="2"/></svg>
      </div>
    </nav>
  </header>

  <main>
    <section class="booking">
      <h2>Your booking agent for</h2>
      <div class="card" style="left:10px">
        <div class="tile stay"><span class="light">book</span><span class="bold">Stay</span></div>
        <p>Find the perfect accommodation to suit your specific needs. Click on book-Stay to view and book our properties online Now!</p>
      </div>
      <div class="card" style="left:330px">
        <div class="tile play"><span class="light">book</span><span class="bold">Play</span></div>
        <p>Secure your Playlist! Karoo Vista has wonderful excurions, activities, shows and festival on offer. Click on BookPlay and book it all ONLINE!</p>
      </div>
      <div class="card" style="left:650px">
        <div class="tile eat"><span class="light">book</span><span class="bold">Eat</span></div>
        <p>Wow! Book your eating experience with us. As always Karoo Vista has the best on offer to enhance your cullinary experience. Click bookEat !</p>
      </div>
    </section>

    <section class="events">
      <h2 class="heading">Special Events and Festivals</h2>
      <div class="rule" style="top:50px"></div>
      <article class="event" style="top:71px">
        <div class="date"><span class="day">01</span><span class="month">August</span></div>
        <h3>Olive Festival - April 2014</h3>
        <p>Lorem ipsum dolor sit amet, consectetur adipisicing elit, sed do eiusmod tempor incididunt ut labore et dolore magna aliqua. Ut enim ad minim veniam, quis nos-trud exercitation ullamco laboris nisi ut aliquip ex ea commodo consequat. Duis aute irure dolor in reprehenderit in voluptate velit esse</p>
      </article>
      <div class="rule" style="top:161px"></div>
      <article class="event" style="top:182px">
        <div class="date"><span class="day">01</span><span class="month">August</span></div>
        <h3>Olive Festival - April 2014</h3>
        <p>Lorem ipsum dolor sit amet, consectetur adipisicing elit, sed do eiusmod tempor incididunt ut labore et dolore magna aliqua. Ut enim ad minim veniam, quis nos-trud exercitation ullamco laboris nisi ut aliquip ex ea commodo consequat. Duis aute irure dolor in reprehenderit in voluptate velit esse</p>
      </article>
    </section>
  </main>

  <footer>
    <div class="contact">
      <h3 class="heading footer-title">Contact Us</h3>
      <div class="contact-line" style="left:0;top:42px">Phone: 0860 555 210<br>E-mail: info@karoovistadirect.test</div>
      <div class="contact-line" style="left:247px;top:42px">Address:<br>&nbsp;Kerk Lane, Karoo Vista</div>
    </div>
    <div class="follow">
      <h3 class="heading footer-title">Follow Us</h3>
      <span class="social" style="left:0;background:#3b5a9a"></span>
      <span class="social" style="left:37px;background:#2aa9e0"></span>
      <span class="social" style="left:78px;background:#d81f1f"></span>
      <span class="social" style="left:115px;background:#2e2e2e"></span>
    </div>

    <div class="siteinfo">
      <div class="legal">©2013 karoovistadirect. All Rights Reserved. Privacy Policy.</div>
      <div class="services">
        <h4>Services</h4>
        <ul>
          <li>Business Directory</li>
          <li>Relevant Links &amp; Websites</li>
          <li>Emergency Numbers</li>
        </ul>
      </div>
      <div class="newsletter">
        <h4>Newslettr Signup</h4>
        <div class="field"></div>
        <div class="signup">SIGHUP</div>
      </div>
    </div>
  </footer>
</body>
</html>
```